Business Management Fortress

Assist with enhancing a powerpoint slide by providing a few design options for consideration. I have a template but open to any creative ideas.

Internal employees and stakeholders

Business Management, Finance, Accounting

• Maintain a fortress, temple, or pyramid schema
• Scenic Background

```html
<!DOCTYPE html>
<html lang="en">
<head>
<meta charset="utf-8">
<title>Business Management Fortress</title>
<link href="https://fonts.googleapis.com/css2?family=Exo+2:ital,wght@0,400;0,600;0,700;0,800;1,800&display=swap" rel="stylesheet">
<style>
  :root {
    --sky-top: #d9eef8;
    --sky-mid: #c9e2ee;
    --sky-low: #e4f2f9;
    --frame: #ffffff;
    --partner-top: #e8707f;
    --partner-bottom: #a50b1a;
    --pillar-top: #eaa10a;
    --pillar-bottom: #d95a08;
    --teal-top: #56d6c0;
    --teal-bottom: #16ac84;
    --base-top: #2a9ac4;
    --base-bottom: #033f78;
    --ink-light: #ffffff;
    --ink-dark: #222222;
  }
  html, body {
    margin: 0;
    padding: 0;
    width: 1200px;
    height: 675px;
    overflow: hidden;
    background: var(--sky-top);
  }
  .slide {
    position: relative;
    width: 1200px;
    height: 675px;
    overflow: hidden;
    font-family: "Exo 2", "Segoe UI", sans-serif;
  }
  .scenery {
    position: absolute;
    inset: 0;
    background:
      linear-gradient(180deg, var(--sky-top) 0%, var(--sky-mid) 45%, #b9cdd3 58%, var(--sky-mid) 64%, var(--sky-low) 100%);
  }
  .pyramid {
    position: absolute;
    inset: 0;
    width: 1200px;
    height: 675px;
  }
  .tier-label {
    font-family: "Exo 2", "Segoe UI", sans-serif;
    font-weight: 700;
    fill: var(--ink-light);
  }
  .tier-label--top { font-size: 42px; font-weight: 800; }
  .tier-label--pillar { font-size: 38px; }
  .tier-label--block { font-size: 29px; }
  .tier-label--base { font-size: 66px; font-weight: 800; font-style: italic; }
  .duty-list {
    font-family: "Exo 2", "Segoe UI", sans-serif;
    font-weight: 400;
    font-size: 27px;
    fill: var(--ink-light);
  }
  .slide-number {
    position: absolute;
    right: 20px;
    bottom: 12px;
    font-size: 11px;
    color: var(--ink-dark);
  }
</style>
</head>
<body>
<div class="slide">
  <div class="scenery" role="img" aria-label="Misty snow-capped mountains reflected in a calm lake"></div>

  <svg class="pyramid" viewBox="0 0 1920 1080" xmlns="http://www.w3.org/2000/svg">
    <defs>
      <linearGradient id="grad-partner" x1="0" y1="0" x2="0" y2="1">
        <stop offset="0" stop-color="var(--partner-top)"/>
        <stop offset="1" stop-color="var(--partner-bottom)"/>
      </linearGradient>
      <linearGradient id="grad-pillar" x1="0" y1="0" x2="0" y2="1">
        <stop offset="0" stop-color="var(--pillar-top)"/>
        <stop offset="1" stop-color="var(--pillar-bottom)"/>
      </linearGradient>
      <linearGradient id="grad-block" x1="0" y1="0" x2="0" y2="1">
        <stop offset="0" stop-color="var(--teal-top)"/>
        <stop offset="1" stop-color="var(--teal-bottom)"/>
      </linearGradient>
      <linearGradient id="grad-base" x1="0" y1="0" x2="0" y2="1">
        <stop offset="0" stop-color="var(--base-top)"/>
        <stop offset="1" stop-color="var(--base-bottom)"/>
      </linearGradient>
    </defs>

    <!-- white frame behind all tiers -->
    <polygon class="frame" fill="var(--frame)" stroke="var(--frame)" stroke-width="34" stroke-linejoin="round"
      points="335,605 560,462 540,422 650,352 638,320 740,258 714,207 965,44 1218,207 1190,258 1290,320 1278,352 1394,422 1370,462 1585,605 960,1000"/>

    <!-- base tier -->
    <polygon class="tier tier--base" fill="url(#grad-base)"
      points="350,605 568,468 965,706 1357,472 1570,605 960,988"/>

    <!-- teal blocks -->
    <polygon class="tier tier--block" fill="url(#grad-block)" points="551,422 660,354 790,436 702,517"/>
    <polygon class="tier tier--block" fill="url(#grad-block)" points="722,535 808,449 952,535 952,676"/>
    <polygon class="tier tier--block" fill="url(#grad-block)" points="976,536 1090,468 1183,548 976,676"/>
    <polygon class="tier tier--block" fill="url(#grad-block)" points="1110,455 1270,354 1381,422 1205,534"/>

    <!-- orange pillars -->
    <polygon class="tier tier--pillar" fill="url(#grad-pillar)" points="658,320 760,258 952,376 952,503"/>
    <polygon class="tier tier--pillar" fill="url(#grad-pillar)" points="976,376 1172,258 1273,320 976,505"/>

    <!-- top tier -->
    <polygon class="tier tier--top" fill="url(#grad-partner)" points="965,58 1202,207 965,354 730,207"/>

    <!-- labels -->
    <text class="tier-label tier-label--top" x="965" y="266" text-anchor="middle">Partner</text>

    <text class="tier-label tier-label--pillar" transform="translate(780,345) rotate(32)">Leader</text>
    <text class="tier-label tier-label--pillar" transform="translate(1022,430) rotate(-32)">Profitability</text>

    <text class="tier-label tier-label--block" transform="translate(633,412) rotate(32)">People</text>
    <text class="tier-label tier-label--block" transform="translate(784,512) rotate(32)">Innovation</text>
    <text class="tier-label tier-label--block" transform="translate(995,595) rotate(-32)">Business</text>
    <text class="tier-label tier-label--block" transform="translate(1012,620) rotate(-32)">Intelligence</text>
    <text class="tier-label tier-label--block" transform="translate(1194,470) rotate(-32)">Strategic</text>
    <text class="tier-label tier-label--block" transform="translate(1210,494) rotate(-32)">Alliances</text>

    <text class="tier-label tier-label--base" transform="translate(572,580) rotate(31)">Fiduciary</text>
    <text class="tier-label tier-label--base" transform="translate(448,610) rotate(31)">Responsibilities</text>

    <text class="duty-list" transform="translate(995,788) rotate(-31)">Accurate Financials / Internal Controls</text>
    <text class="duty-list" transform="translate(1012,823) rotate(-31)">Brand Protection / Compliance / Ethics</text>
    <text class="duty-list" transform="translate(1148,797) rotate(-31)">Cost Management</text>
  </svg>

  <div class="slide-number">C9</div>
</div>
</body>
</html>
```